TL - business card

Tallow Partners is an insurance brokerage firm, inovative, proactive, vigorous, which aims to become the leader of the insurance brokers in Anfrica. We should like to get some designs which should be avoided also in Gray / Metallic for the Administration and Orange / Blue for the Managers (ike in the picture sent). The Blue / Green logo is not the correct one, but the source of the file. Please adjust the color accordingly for the business cards. 1 / Orange / Blue 2 / Gray / Metallic We want something classic but which is transmitted strenght, inovation, modernity and most of all, rapidity. We want something start-up like, very punchy and catching eye remaining profesional at the same time. Name: Dorian Whitlock Function: Managing Director Address: N ° 17/18 Rua Veloso - R / C 2B Direita - Bairro Mutamba - Luanda Tel: (+244) 947 582 316 Email: dorian.whitlock@tallow-p.example Website: www.tallow-p. example We want classic in the front and creative, colorfull at the back. The cards will be printed in relief, with very high quality of paper.
Insurance Broker
Colors
Designer to choose colors to be used in the design.

```html
<!DOCTYPE html>
<html lang="en">
<head>
<meta charset="utf-8">
<title>Tallow Partners – Business Card</title>
<link href="https://fonts.googleapis.com/css2?family=Arimo:wght@400;700&display=swap" rel="stylesheet">
<style>
  :root {
    --stage: #2e2e2e;
    --card-dark: #2a2a2a;
    --card-dark-edge: #353535;
    --emboss: #1a1a1a;
    --white: #ffffff;
    --paper: #f4f4f4;
    --green: #1f8a3c;
    --green-deep: #16702f;
    --orange: #e2671f;
    --orange-deep: #a9480f;
    --ink-light: #ffffff;
    --ink-dark: #12331d;
  }
  * { margin: 0; padding: 0; box-sizing: border-box; }
  html, body { width: 1200px; height: 997px; overflow: hidden; }
  body {
    background: var(--stage);
    font-family: "Arimo", Arial, sans-serif;
    position: relative;
  }
  .card {
    position: absolute;
    top: 340px;
    width: 540px;
    height: 310px;
    border-radius: 22px;
    overflow: hidden;
  }
  .card-front {
    left: 45px;
    background: linear-gradient(160deg, var(--card-dark-edge), var(--card-dark));
    display: flex;
    align-items: center;
    justify-content: center;
    gap: 16px;
  }
  .front-mark {
    width: 58px; height: 58px;
    border-radius: 50%;
    background: var(--emboss);
  }
  .front-name {
    color: var(--emboss);
    font-weight: 700;
    font-size: 40px;
    letter-spacing: 1px;
    text-transform: uppercase;
  }
  .card-back { left: 615px; background: var(--paper); }
  .card-back svg.bands { position: absolute; inset: 0; }
  .brand {
    position: absolute;
    top: 72px; left: 0; right: 0;
    display: flex; justify-content: center; align-items: center; gap: 10px;
  }
  .brand-mark { width: 30px; height: 30px; border-radius: 50%; background: var(--orange); }
  .brand-name {
    color: var(--green);
    font-weight: 700;
    font-size: 30px;
    text-transform: uppercase;
  }
  .person {
    position: absolute;
    top: 146px; left: 0; right: 0;
    text-align: center;
    color: var(--ink-light);
  }
  .person-name { font-weight: 700; font-size: 17px; letter-spacing: .5px; text-transform: uppercase; }
  .person-role { font-size: 14px; margin-top: 2px; }
  .address {
    position: absolute;
    right: 24px; top: 206px;
    text-align: right;
    color: var(--ink-dark);
    font-size: 11.5px;
    line-height: 1.35;
  }
  .address .company { font-weight: 700; font-size: 12.5px; }
  .contacts {
    position: absolute;
    left: 24px; bottom: 20px;
    list-style: none;
    color: var(--ink-light);
    font-size: 13px;
    line-height: 1.55;
  }
  .contacts li { display: flex; align-items: center; gap: 8px; }
  .contacts svg { width: 12px; height: 12px; fill: var(--ink-light); flex: none; }
</style>
</head>
<body>

<section class="card card-front" aria-label="Card front">
  <span class="front-mark"></span>
  <span class="front-name">Tallow Partners</span>
</section>

<section class="card card-back" aria-label="Card back">
  <svg class="bands" viewBox="0 0 540 310" preserveAspectRatio="none">
    <rect x="0" y="172" width="540" height="138" fill="var(--green)"/>
    <rect x="0" y="166" width="540" height="7" fill="var(--orange)"/>
    <polygon points="110,173 140,138 400,138 430,173" fill="var(--orange-deep)"/>
    <polygon points="122,200 150,138 390,138 418,200" fill="var(--orange)"/>
  </svg>

  <div class="brand">
    <span class="brand-mark"></span>
    <span class="brand-name">Tallow Partners</span>
  </div>

  <div class="person">
    <div class="person-name">Dorian Whitlock</div>
    <div class="person-role">Managing Director</div>
  </div>

  <div class="address">
    <div class="company">Tallow Partners Pvt Ltd</div>
    <div>N ° 17/18 Rua Veloso - R / C 2B Direita</div>
    <div>Bairro Mutamba - Luanda</div>
  </div>

  <ul class="contacts">
    <li>
      <svg viewBox="0 0 12 12"><path d="M1 3c0-1 1-2 2-2h1l1 2.5-1.2 1a6 6 0 0 0 2.7 2.7l1-1.2L10 7v1c0 1-1 2-2 2C4 10 1 7 1 3z"/></svg>
      (+244) 947 582 316
    </li>
    <li>
      <svg viewBox="0 0 12 12"><path d="M0 2h12v8H0z M1 3l5 3.5L11 3v-.2H1z" fill-rule="evenodd"/></svg>
      dorian.whitlock@tallow-p.example
    </li>
    <li>
      <svg viewBox="0 0 12 12"><path d="M6 1l6 5h-2v5H7.5V8h-3v3H2V6H0z"/></svg>
      www.tallow-p. example
    </li>
  </ul>
</section>

</body>
</html>
```